Harborview Estates Business Card for Apartment Buildings

Create business cards for resident managers who run apartment buildings. The audience is the public who are searching for apartment rentals, and current residents who live at the apartment building. Key design element will be incorporating the company logo, however, the logo cannot dominate. The building name and manager name are more important than the logo. Current business card design leaves little room for copy, so we may need to reduce the size on the current card to allow for more space for copy.

Target Market(s)

Adults 18-65 years of age, who are looking for an apartment rental, plus current residents who live at our apartment buildings.

Industry/Entity Type

Property Management

Contact Information for Business Card

A major design element will be use of the company logo. Important property and manager contact information must be part of the design. The size of the logo will need to be reduced to make room for building and manager contact copy.

Font styles to use
Sans Serif

Colors
3176b5
000000
959595
ffffff

Requirements
Must have
• 1) Incorporate the company logo.
• 2) Use the company colors (dark blue, black/grey, over white).
• 3) FEATURE THE BUILDING NAME
• 4) FEATURE THE MANAGER NAME
• 5) The company name is less important than BUILDING and MANAGER
• 6) Manager contact information
• **SEE ATTACHED CREATIVE BRIEF**
Nice to have
• 1) Back of card logo watermark
• 2) Ability to write notes on back of carfd
Should not have
• Avoid letting the company logo dominate the card, the building name and manager are more important than the company logo.

```html
<!DOCTYPE html>
<html lang="en">
<head>
<meta charset="utf-8">
<title>Harborview Estates – Resident Manager Card</title>
<link rel="stylesheet" href="https://fonts.googleapis.com/css2?family=Roboto:wght@400;700&display=swap">
<style>
  :root {
    --brand-blue: #1f66ab;
    --ink: #333333;
    --grey: #959595;
    --paper: #ffffff;
    --backdrop: #e6e6e6;
    --watermark: #e4e7f0;
  }
  * { box-sizing: border-box; margin: 0; padding: 0; }
  html, body { width: 1200px; height: 960px; overflow: hidden; }
  body {
    background: var(--backdrop);
    font-family: "Roboto", Arial, sans-serif;
    position: relative;
  }
  .card {
    position: absolute;
    left: 272px;
    width: 655px;
    height: 373px;
    background: var(--paper);
    border-radius: 24px;
    box-shadow: 0 4px 10px rgba(0,0,0,0.25);
  }
  .card--front { top: 81px; }
  .card--back { top: 506px; }

  .brand {
    position: absolute;
    top: 64px;
    left: 0; right: 0;
    display: flex;
    justify-content: center;
    align-items: center;
    gap: 12px;
  }
  .brand__dot {
    width: 22px; height: 22px;
    border-radius: 50%;
    background: var(--brand-blue);
  }
  .brand__name {
    font-size: 28px;
    font-weight: 700;
    color: var(--brand-blue);
    letter-spacing: 0.3px;
  }

  .manager {
    position: absolute;
    top: 160px;
    left: 0; right: 0;
    text-align: center;
  }
  .manager__name {
    font-size: 22px;
    font-weight: 700;
    color: var(--brand-blue);
    line-height: 28px;
  }
  .manager__title {
    font-size: 16px;
    color: var(--ink);
    line-height: 22px;
  }

  .property {
    position: absolute;
    top: 245px;
    right: 345px;
    text-align: right;
    font-size: 15px;
    line-height: 22px;
    color: var(--ink);
  }
  .property__name { font-weight: 700; color: var(--brand-blue); }
  .property__web { color: var(--brand-blue); letter-spacing: 1px; }

  .divider {
    position: absolute;
    left: 328px;
    top: 247px;
    width: 1.5px;
    height: 84px;
    background: var(--ink);
  }

  .contacts {
    position: absolute;
    top: 245px;
    left: 347px;
    list-style: none;
    font-size: 15px;
    line-height: 22px;
    color: var(--ink);
  }
  .contacts li { display: flex; align-items: center; gap: 9px; }
  .contacts svg { width: 15px; height: 15px; flex: none; fill: var(--brand-blue); }

  .watermark {
    position: absolute;
    inset: 0;
    display: flex;
    justify-content: center;
    align-items: center;
    gap: 18px;
  }
  .watermark__dot {
    width: 60px; height: 60px;
    border-radius: 50%;
    background: var(--watermark);
  }
  .watermark__name {
    font-size: 48px;
    font-weight: 700;
    color: var(--watermark);
  }
</style>
</head>
<body>
  <section class="card card--front">
    <div class="brand">
      <span class="brand__dot"></span>
      <span class="brand__name">Harborview Estates</span>
    </div>

    <div class="manager">
      <p class="manager__name">Marisol Delgado</p>
      <p class="manager__title">Resident Manager</p>
    </div>

    <div class="property">
      <p class="property__name">Cedar Court Apartments</p>
      <p>2485 Linden Avenue</p>
      <p>Bayside, CA 92110</p>
      <p class="property__web">www.harborviewestates.com</p>
    </div>

    <div class="divider"></div>

    <ul class="contacts">
      <li>
        <svg viewBox="0 0 16 16" aria-label="Phone"><path d="M4.5 1.5l2 3-1.3 1.5c.8 1.9 2.1 3.3 4 4.2l1.5-1.3 3 2-1.2 2.6C7.3 13.2 2.8 8.7 2 3z"/></svg>
        <span>555-214-3870</span>
      </li>
      <li>
        <svg viewBox="0 0 16 16" aria-label="Fax"><rect x="4" y="1" width="8" height="4"/><rect x="1" y="6" width="14" height="6" rx="1.5"/><rect x="4" y="10" width="8" height="5" fill="#fff" stroke="#1f66ab" stroke-width="1.2"/></svg>
        <span>555-214-3871</span>
      </li>
      <li>
        <svg viewBox="0 0 16 16" aria-label="Mobile"><path d="M4.5 1h7a1 1 0 0 1 1 1v12a1 1 0 0 1-1 1h-7a1 1 0 0 1-1-1V2a1 1 0 0 1 1-1zm1 2v8.5h5V3z"/></svg>
        <span>555-608-4192</span>
      </li>
      <li>
        <svg viewBox="0 0 16 16" aria-label="Email"><path d="M1 3.5h14v9H1z M1.8 4.2L8 9l6.2-4.8" stroke="#fff" stroke-width="1"/></svg>
        <span>marisol@harborviewestates.com</span>
      </li>
    </ul>
  </section>

  <section class="card card--back">
    <div class="watermark">
      <span class="watermark__dot"></span>
      <span class="watermark__name">Harborview Estates</span>
    </div>
  </section>
</body>
</html>
```